Become a Mentor - For Musicians, Artists, Producers and Teachers

Here is the full creative brief:

https://files.quorvant.com/sheets/d/7kTbWmQa2_pLRz9XcN4eHs8JuYd3FoVgA6iBnCqE/view?mode=shared

Here is the background image file: https://www.stashvel.com/sh/48kdmwtnb7yrs2p/AAZm3kLPQwTx8VnHRe4jBcDu?dl=0

LOGO:
https://www.stashvel.com/sh/k382fubotn7wq6/AAJhT5LsRy2D-mKzPX9CvGhNb?dl=0

```html
<!DOCTYPE html>
<html lang="en">
<head>
<meta charset="utf-8">
<title>Become a Mentor Today – Northwind School of Music</title>
<link href="https://fonts.googleapis.com/css2?family=Bebas+Neue&family=Kaushan+Script&family=Lato:ital,wght@0,400;0,700;1,900&display=swap" rel="stylesheet">
<style>
  :root {
    --page: #ececec;
    --navy: #0b0e2c;
    --navy-deep: #05071a;
    --red: #c8141d;
    --red-dark: #8e0c12;
    --pink: #ff3d5e;
    --blue: #1e9be0;
    --white: #ffffff;
    --muted: #c9cde0;
  }
  * { box-sizing: border-box; margin: 0; padding: 0; }
  html, body { width: 1200px; height: 830px; overflow: hidden; background: var(--page); }
  body { position: relative; font-family: "Lato", sans-serif; }

  .poster {
    position: absolute; left: 320px; top: 19px; width: 560px; height: 792px;
    overflow: hidden;
    background: radial-gradient(ellipse at 70% 85%, #1a2150 0%, var(--navy) 45%, var(--navy-deep) 100%);
    box-shadow: 0 4px 14px rgba(0,0,0,.25);
  }

  .headline { position: absolute; left: 28px; top: 22px; font-family: "Bebas Neue", sans-serif; line-height: .9; }
  .headline-small { display: block; font-size: 38px; color: var(--white); letter-spacing: 1px; }
  .headline-big {
    display: block; font-size: 98px; letter-spacing: 1px;
    background: linear-gradient(180deg, #ffffff 0%, #d9d9d9 45%, #8f8f8f 55%, #e6e6e6 100%);
    -webkit-background-clip: text; background-clip: text; color: transparent;
  }

  .brand { position: absolute; right: 24px; top: 64px; display: flex; align-items: center; gap: 8px; }
  .brand-dot { width: 14px; height: 14px; border-radius: 50%; background: var(--blue); }
  .brand-name { font-family: "Lato", sans-serif; font-weight: 700; font-size: 15px; color: var(--white); letter-spacing: 1.5px; text-transform: uppercase; line-height: 1.2; text-align: left; }

  .photo {
    position: absolute; left: 0; top: 143px; width: 560px; height: 450px;
    background: linear-gradient(100deg, #e6ddd0 0%, #8a8378 35%, #4b4744 60%, #2a2a30 100%);
    clip-path: polygon(0 6%, 12% 3%, 30% 5%, 48% 2%, 66% 4%, 82% 1%, 100% 3%, 100% 100%, 0 100%);
  }

  .band { position: absolute; left: 0; top: 440px; width: 560px; height: 215px; }

  .become { position: absolute; left: 200px; top: 425px; font-family: "Kaushan Script", cursive; font-size: 54px; color: var(--white); transform: rotate(-4deg); }
  .mentor { position: absolute; left: 38px; top: 488px; font-family: "Bebas Neue", sans-serif; font-size: 104px; color: var(--white); letter-spacing: 1px; transform: rotate(-3deg); text-shadow: 0 2px 4px rgba(0,0,0,.4); }

  .pitch { position: absolute; left: 0; top: 612px; width: 560px; text-align: center; color: var(--white); font-size: 18.5px; line-height: 25px; }
  .pitch .musicians { color: var(--pink); }
  .pitch .artists { color: #e8242b; }
  .pitch .producers { color: var(--blue); }

  .contact { position: absolute; left: 36px; top: 690px; font-size: 10.5px; color: var(--muted); line-height: 15px; }
  .contact-name { color: var(--blue); font-size: 13px; font-weight: 700; text-transform: uppercase; }
  .contact-row { display: flex; align-items: center; gap: 6px; }
  .contact-row svg { width: 8px; height: 8px; }

  .social { position: absolute; left: 20px; top: 757px; display: flex; align-items: center; gap: 7px; font-size: 8.5px; color: var(--muted); }
  .social-dot { width: 22px; height: 22px; border-radius: 50%; background: var(--red); }

  .apply {
    position: absolute; left: 320px; top: 685px; width: 210px; height: 52px;
    border: 2px solid var(--white); border-radius: 7px;
    background: linear-gradient(180deg, #e32a30 0%, var(--red) 50%, var(--red-dark) 100%);
    display: flex; align-items: center; justify-content: center;
    font-weight: 900; font-style: italic; font-size: 32px; color: var(--white); letter-spacing: .5px;
  }
  .call { position: absolute; left: 320px; top: 746px; width: 210px; text-align: center; color: var(--white); font-size: 24px; font-weight: 700; }
</style>
</head>
<body>
  <main class="poster">
    <h1 class="headline">
      <span class="headline-small">Start Your</span>
      <span class="headline-big">Career</span>
    </h1>

    <div class="brand">
      <span class="brand-dot"></span>
      <span class="brand-name">Northwind<br>School of Music</span>
    </div>

    <div class="photo" role="img" aria-label="Photo of two young musicians talking in a recording studio with a mixing desk and monitor speaker"></div>

    <svg class="band" viewBox="0 0 560 215" preserveAspectRatio="none" aria-hidden="true">
      <polygon points="0,60 120,52 260,40 420,22 560,8 560,140 430,152 300,164 150,176 0,190" fill="var(--red)"/>
      <polygon points="0,180 160,168 320,156 560,132 560,150 300,172 0,200" fill="var(--red-dark)" opacity=".7"/>
    </svg>

    <div class="become">Become a</div>
    <div class="mentor">Mentor Today</div>

    <p class="pitch">
      Turn your skills and passion for music into a career<br>
      Designed for <span class="musicians">Musicians</span>, <span class="artists">Artists</span>, <span class="producers">Producers &amp; Teachers</span>
    </p>

    <div class="contact">
      <div class="contact-name">Dana Kell</div>
      <div class="contact-row"><svg viewBox="0 0 10 10"><path d="M2 1l2 2-1 1.5c.8 1.5 1.5 2.2 3 3L7.5 6l2 2-1.5 1.5C4 9 1 6 .5 2z" fill="var(--blue)"/></svg>0400 123 456, (03) 9000 1234</div>
      <div class="contact-row"><svg viewBox="0 0 10 10"><rect x="1" y="2" width="8" height="6" fill="none" stroke="var(--blue)"/><path d="M1 2l4 3 4-3" fill="none" stroke="var(--blue)"/></svg>dana@northwindmusic.com.au</div>
      <div class="contact-row"><svg viewBox="0 0 10 10"><circle cx="5" cy="5" r="4" fill="none" stroke="var(--blue)"/><path d="M1 5h8M5 1v8" stroke="var(--blue)"/></svg>www.northwindmusic.com.au</div>
    </div>

    <div class="social">Find us on <span class="social-dot"></span><span class="social-dot"></span></div>

    <div class="apply">APPLY NOW</div>
    <div class="call">Call 1300 XXX XXX</div>
  </main>
</body>
</html>
```